Website for BrightlineLabs presentation

We need a new website, ideally as a wordpress there, for BrightlineLabs - we focus on machine learning, big data, data science and data analytics. This website should have two main sections - team presentation, introduction and offered services as static pages, and a blog section.

Target Market(s)

Companies which would like to hire the consultants for data science

Industry/Entity Type

Data Service

Font styles to use
Sans Serif

Colors

Designer to choose colors to be used in the design.

Requirements
Must have
• Wordpress template, blog and presentation pages, nice background images, incorporate the existing logo from brief
Nice to have
• match the word and ppt existing templates for brightline labs

```html
<!DOCTYPE html>
<html lang="en">
<head>
<meta charset="utf-8">
<title>BrightlineLabs</title>
<link href="https://fonts.googleapis.com/css2?family=Montserrat:wght@400;500;600;700&family=Open+Sans:wght@400;600&display=swap" rel="stylesheet">
<style>
:root{
  --blue:#1b76c9;
  --blue-deep:#0b4f9e;
  --blue-dark:#083a78;
  --blue-light:#3fa0ef;
  --title:#1a6ab8;
  --text:#555d66;
  --muted:#777;
  --white:#fff;
  --line:#d7dde3;
  --footer:#2b2f33;
}
*{margin:0;padding:0;box-sizing:border-box}
html,body{width:1200px;height:4138px;overflow:hidden}
body{position:relative;background:var(--white);font-family:'Open Sans',Arial,sans-serif;color:var(--text)}
.abs{position:absolute}
h1,h2,h3,.nav,.brand{font-family:'Montserrat',Arial,sans-serif}

/* header */
.site-header{left:0;top:0;width:1200px;height:105px;background:var(--white);z-index:3}
.brand{position:absolute;left:132px;top:28px;display:flex;align-items:center;gap:12px;color:var(--blue-deep);font-weight:700;font-size:20px;line-height:1.1}
.brand-mark{width:34px;height:34px;background:var(--blue);border-radius:4px}
.nav{position:absolute;right:132px;top:42px;display:flex;gap:34px;font-size:13px;font-weight:500;color:#444}
.nav .active{color:var(--blue)}

/* hero */
.hero{left:0;top:105px;width:1200px;height:590px;clip-path:polygon(0 0,100% 0,100% 515px,0 590px);
  background:radial-gradient(circle at 70% 40%,#5fb8ff 0,#1d7fd6 35%,#0d4e9e 80%)}
.hero-brand{left:132px;top:95px;color:var(--white);font-family:'Montserrat',sans-serif;font-weight:700;font-size:26px}
.hero-circle{border-radius:50%;background:var(--white)}
.arrow{top:225px;color:var(--white);font-size:40px;font-family:'Montserrat',sans-serif}
.hero h1{left:132px;top:315px;color:var(--white);font-size:33px;font-weight:600}
.hero .sub{left:132px;top:360px;color:var(--white);font-size:25px;font-family:'Montserrat',sans-serif}
.hero .tag{left:132px;top:400px;background:var(--white);color:#333;font-size:13px;font-family:'Montserrat',sans-serif;padding:14px 20px;font-weight:500}

/* generic */
.section-title{font-size:32px;font-weight:700;color:var(--title);text-transform:uppercase}

/* welcome */
.welcome-title{left:132px;top:765px}
.welcome-image{left:132px;top:828px;width:453px;height:303px;background:linear-gradient(135deg,#35506e,#6b8aa8 50%,#1f3550)}
.welcome-text{left:621px;top:823px;width:441px;font-size:12.5px;line-height:24px;color:var(--text)}

/* services */
.services{left:0;top:1214px;width:1200px;height:1050px;clip-path:polygon(0 83px,100% 0,100% 980px,0 1050px);
  background:radial-gradient(circle at 30% 30%,#2f8ae0,#0f5cb4 55%,#08448c)}
.services-title{left:132px;top:1365px;color:var(--white)}
.service{left:0;width:1200px;height:140px}
.service .ring{position:absolute;width:133px;height:133px;border:2px solid rgba(255,255,255,.7);border-radius:50%;display:flex;align-items:center;justify-content:center}
.service .ring span{width:98px;height:98px;border-radius:50%;background:var(--white);display:flex;align-items:center;justify-content:center}
.service h3{position:absolute;top:18px;color:var(--white);font-size:20px;font-weight:500}
.service .rule{position:absolute;top:50px;right:138px;height:2px;background:rgba(255,255,255,.75)}
.service .rule::after{content:"";position:absolute;right:-7px;top:-6px;width:14px;height:14px;border-radius:50%;background:var(--white)}
.service p{position:absolute;top:62px;right:138px;color:var(--white);font-size:10.5px;line-height:18px}

/* team */
.team-title{left:132px;top:2332px}
.member{top:2393px;width:160px;text-align:center}
.member .photo{width:160px;height:160px;background:linear-gradient(180deg,#d9d9d9,#9c9c9c)}
.member h3{margin-top:14px;font-size:14px;font-weight:500;color:var(--title)}
.member p{margin-top:4px;font-size:10px;line-height:14px;color:var(--muted)}

/* blog */
.blog{left:0;top:2692px;width:1200px;height:925px;clip-path:polygon(0 80px,100% 0,100% 870px,0 925px);
  background:radial-gradient(circle at 60% 40%,#2a86dc,#0f5cb4 55%,#08448c)}
.blog-title{left:132px;top:2848px;color:var(--white)}
.post{top:2912px;width:436px;height:524px;background:var(--white)}
.post .thumb{height:254px}
.post h3{margin:28px 28px 0;font-size:19px;font-weight:500;line-height:28px;color:#222}
.post time{display:block;margin:16px 28px 0;font-size:11px;color:var(--blue)}
.post p{margin:12px 28px 0;font-size:10.5px;line-height:17px;color:var(--text)}
.post .more{display:inline-block;margin:22px 28px 0;border:1px solid var(--line);padding:8px 14px;font-size:10.5px;color:#555}

/* contact */
.contact-title{left:132px;top:3678px}
.field{height:37px;border:1px solid var(--line);font-size:10.5px;color:#999;padding:11px 12px}
.submit{left:563px;top:3858px;width:74px;height:37px;background:var(--blue);color:var(--white);font-family:'Montserrat',sans-serif;font-weight:600;font-size:12px;display:flex;align-items:center;justify-content:center}

/* footer */
.site-footer{left:0;top:3950px;width:1200px;height:188px;background:var(--footer);clip-path:polygon(0 50px,100% 0,100% 100%,0 100%)}
.footer-nav{left:132px;top:4060px;font-size:10.5px;color:#ccc}
.copyright{left:132px;top:4088px;font-size:10.5px;color:#aaa}
.social{top:4063px;width:26px;height:26px;border-radius:50%}
</style>
</head>
<body>

<header class="abs site-header">
  <div class="brand"><span class="brand-mark"></span>BRIGHTLINE<br>LABS</div>
  <nav class="nav"><span class="active">HOME</span><span>ABOUT US</span><span>SERVICES</span><span>BLOG</span><span>CONTACT US</span></nav>
</header>

<section class="abs hero" role="img" aria-label="Blue circuit board background with glowing nodes">
  <div class="abs hero-brand">BRIGHTLINE LABS</div>
  <div class="abs hero-circle" style="left:972px;top:58px;width:96px;height:96px"></div>
  <div class="abs hero-circle" style="left:772px;top:220px;width:96px;height:96px"></div>
  <div class="abs arrow" style="left:45px">&#8249;</div>
  <div class="abs arrow" style="right:45px">&#8250;</div>
  <h1 class="abs">Cloudway Business Analytics and AI</h1>
  <div class="abs sub">Building Solutions - Environment Setup</div>
  <div class="abs tag">CLOUDWAY MACHINE LEARNING AND DATA SCIENCE TEAM</div>
</section>

<h2 class="abs section-title welcome-title">Welcome to BrightlineLabs</h2>
<div class="abs welcome-image" role="img" aria-label="Hand touching a hexagon diagram of machine learning topics"></div>
<p class="abs welcome-text">Nam lobortis, purus et fringilla tempus, risus eros dignissim diam, eget finibus sem risus sit amet eros. Vestibulum facilisis dolor at purus tincidunt porta. Nam fringilla nulla vel nisl condimentum, dapibus condimentum enim porta. Phasellus blandit quam a ipsum gravida dapibus. Cras sed augue tortor. Suspendisse elit ligula, iaculis dignissim justo eu, vestibulum venenatis elit. Sed egestas, nisl id cursus ultricies, turpis orci rhoncus odio, id tristique odio ex in lacus. Nam suscipit sapien eget blandit sollicitudin. Donec quis ex semper, consequat ligula at, efficitur lacus. Phasellus elementum lacinia quam non pellentesque. Aliquam malesuada eros sit amet turpis scelerisque maximus. Maecenas lobortis iaculis efficitur. Nulla facilisi. Vestibulum pharetra diam ex, in posuere purus efficitur ac. Mauris placerat eros lorem, vel egestas mi mattis eget. Donec a nisl vel ante tristique mollis nec quis est.</p>

<section class="abs services" role="img" aria-label="Blue network pattern background"></section>
<h2 class="abs section-title services-title">Services</h2>

<div class="abs service" style="top:1437px">
  <div class="ring" style="left:132px;top:0"><span><svg width="46" height="46" viewBox="0 0 46 46" fill="none" stroke="#1b76c9" stroke-width="2"><circle cx="23" cy="20" r="12"/><path d="M17 34h12M19 39h8"/></svg></span></div>
  <h3 style="left:290px;top:30px">Machine Learning</h3>
  <div class="rule" style="left:265px;top:62px"></div>
  <p style="left:290px;top:72px">Mauris pulvinar volutpat ipsum, nec sodales arcu dignissim sed. Phasellus congue dapibus sapien eu tincidunt. Duis congue mauris nec tortor elementum, scelerisque posuere felis placerat. In a ligula eu nisi sodales sollicitudin. Curabitur dignissim malesuada nibh ut euismod. In tincidunt magna nunc, id iaculis mauris condimentum et. Vestibulum id scelerisque turpis, at vulputate neque.</p>
</div>

<div class="abs service" style="top:1617px">
  <div class="ring" style="left:165px;top:0"><span><svg width="46" height="46" viewBox="0 0 46 46" fill="none" stroke="#1b76c9" stroke-width="2"><rect x="10" y="8" width="26" height="8"/><rect x="10" y="19" width="26" height="8"/><rect x="10" y="30" width="26" height="8"/></svg></span></div>
  <h3 style="left:322px;top:30px">Big Data</h3>
  <div class="rule" style="left:298px;top:62px"></div>
  <p style="left:322px;top:72px">Mauris pulvinar volutpat ipsum, nec sodales arcu dignissim sed. Phasellus congue dapibus sapien eu tincidunt. Duis congue mauris nec tortor elementum, scelerisque posuere felis placerat. In a ligula eu nisi sodales sollicitudin. Curabitur dignissim malesuada nibh ut euismod. In tincidunt magna nunc, id iaculis mauris condimentum et. Vestibulum id scelerisque turpis, at vulputate neque.</p>
</div>

<div class="abs service" style="top:1797px">
  <div class="ring" style="left:132px;top:0"><span><svg width="46" height="46" viewBox="0 0 46 46" fill="none" stroke="#1b76c9" stroke-width="2"><ellipse cx="18" cy="12" rx="9" ry="4"/><path d="M9 12v18c0 2 4 4 9 4s9-2 9-4V12"/><path d="M27 22h10v14H27"/></svg></span></div>
  <h3 style="left:290px;top:30px">Data Science</h3>
  <div class="rule" style="left:265px;top:62px"></div>
  <p style="left:290px;top:72px">Mauris pulvinar volutpat ipsum, nec sodales arcu dignissim sed. Phasellus congue dapibus sapien eu tincidunt. Duis congue mauris nec tortor elementum, scelerisque posuere felis placerat. In a ligula eu nisi sodales sollicitudin. Curabitur dignissim malesuada nibh ut euismod. In tincidunt magna nunc, id iaculis mauris condimentum et. Vestibulum id scelerisque turpis, at vulputate neque.</p>
</div>

<div class="abs service" style="top:1977px">
  <div class="ring" style="left:165px;top:0"><span><svg width="46" height="46" viewBox="0 0 46 46" fill="none" stroke="#1b76c9" stroke-width="2"><circle cx="20" cy="20" r="12"/><path d="M29 29l9 9M14 24l4-5 4 3 5-7"/></svg></span></div>
  <h3 style="left:322px;top:30px">Data Analytics</h3>
  <div class="rule" style="left:298px;top:62px"></div>
  <p style="left:322px;top:72px">Mauris pulvinar volutpat ipsum, nec sodales arcu dignissim sed. Phasellus congue dapibus sapien eu tincidunt. Duis congue mauris nec tortor elementum, scelerisque posuere felis placerat. In a ligula eu nisi sodales sollicitudin. Curabitur dignissim malesuada nibh ut euismod. In tincidunt magna nunc, id iaculis mauris condimentum et. Vestibulum id scelerisque turpis, at vulputate neque.</p>
</div>

<h2 class="abs section-title team-title">Team</h2>
<div class="abs member" style="left:132px"><div class="photo" role="img" aria-label="Portrait of William"></div><h3>William</h3><p>Donec aliquam quam eget<br>euismod dictum</p></div>
<div class="abs member" style="left:326px"><div class="photo" role="img" aria-label="Portrait of Emma"></div><h3>Emma</h3><p>In pulvinar nibh non<br>velit maximus</p></div>
<div class="abs member" style="left:519px"><div class="photo" role="img" aria-label="Portrait of Ethan"></div><h3>Ethan</h3><p>Nunc pellentesque diam et<br>lacus pellentesque</p></div>
<div class="abs member" style="left:713px"><div class="photo" role="img" aria-label="Portrait of Isabella"></div><h3>Isabella</h3><p>Aliquam dignissim nisi<br>nec mauris porta</p></div>
<div class="abs member" style="left:906px"><div class="photo" role="img" aria-label="Portrait of Alexander"></div><h3>Alexander</h3><p>Nulla porttitor nibh ut<br>mi feugiat rhoncus</p></div>

<section class="abs blog" role="img" aria-label="Blue network pattern background"></section>
<h2 class="abs section-title blog-title">Blog</h2>
<article class="abs post" style="left:132px">
  <div class="thumb" role="img" aria-label="Glowing blue circuit brain" style="background:radial-gradient(circle,#3aa0ff,#0a3f8a 70%,#041d4a)"></div>
  <h3>Integer sapien felis, sodales ut lacus non dignissim pretium nibh</h3>
  <time>3 Jul, 2018</time>
  <p>Pellentesque magna orci, placerat et nisl at, porta ultrices turpis. Fusce in eros non orci posuere viverra ut a lectus. In mattis, lorem sit amet consequat placerat, augue nulla mollis turpis, vitae egestas est tellus in nulla. Vestibulum convallis rutrum tincidunt. Aenean sit amet suscipit leo.</p>
  <span class="more">Read More</span>
</article>
<article class="abs post" style="left:635px">
  <div class="thumb" role="img" aria-label="Dark blue data code display" style="background:linear-gradient(135deg,#0a1f4a,#1f5fb0 55%,#0a1a3a)"></div>
  <h3>Nulla cursus ac sapien eget porttitor. Pellentesque accumsan metus elementum</h3>
  <time>3 Jul, 2018</time>
  <p>Pellentesque magna orci, placerat et nisl at, porta ultrices turpis. Fusce in eros non orci posuere viverra ut a lectus. In mattis, lorem sit amet consequat placerat, augue nulla mollis turpis, vitae egestas est tellus in nulla. Vestibulum convallis rutrum tincidunt. Aenean sit amet suscipit leo.</p>
  <span class="more">Read More</span>
</article>

<h2 class="abs section-title contact-title">Contact Us</h2>
<div class="abs field" style="left:132px;top:3740px;width:219px">Name</div>
<div class="abs field" style="left:371px;top:3740px;width:219px">Email Address</div>
<div class="abs field" style="left:610px;top:3740px;width:219px">Phone Number</div>
<div class="abs field" style="left:849px;top:3740px;width:219px;display:flex;justify-content:space-between">Service for <span>&#9662;</span></div>
<div class="abs field" style="left:132px;top:3803px;width:936px">Message</div>
<div class="abs submit">SUBMIT</div>

<footer class="abs site-footer"></footer>
<div class="abs footer-nav">Home &nbsp;|&nbsp; About Us &nbsp;|&nbsp; Services &nbsp;|&nbsp; Blog &nbsp;|&nbsp; Contact Us</div>
<div class="abs copyright">Copyright © 2018 BrightlineLabs. All rights reserved.</div>
<div class="abs social" style="left:1008px;background:#3b5fa8"></div>
<div class="abs social" style="left:1040px;background:#2ea0e6"></div>

</body>
</html>
```